Velmora Consulting Business

** Please add the content information from my old business card
1. I would like to see a two sided business card with both options with the 1st Option--Tallow Spire-new WHITE BACKGROUND LOGO
2 nd Option-Tallow Spire - new BLACK- Background Logo
3rd -Option a business card with my Photo on the card
Please add the new word to the card information:
EXECUTION
AS THE OWNER'S REP
WE AIM TO ACHIEVE YOUR
INFRASTRUCTURE VISION with
OUR SPECIALIZATION & EXECUTION in:

FUNDING Planning
BUSINESS Planning
INFRASTRUCTURE Planning
PROJECT Management
Since 2012
_____________________________________________________________________
I want to get spot uv raised printing. I was liking a a nice rich white linen paper stock with black writing & NOT A COLORED CARD other than a variety of white or black cards concept

```html
<!DOCTYPE html>
<html lang="en">
<head>
<meta charset="utf-8">
<title>Velmora Consulting – Business Card</title>
<link href="https://fonts.googleapis.com/css2?family=Lato:wght@400;700;900&display=swap" rel="stylesheet">
<style>
  :root {
    --backdrop: #2b2b2b;
    --card: #2f2f30;
    --card-edge: #3a3a3b;
    --ink: #ffffff;
    --ink-soft: #d9d9d9;
    --ink-muted: #8d8d8d;
    --accent: #e0182d;
  }
  * { box-sizing: border-box; margin: 0; padding: 0; }
  html, body { width: 1200px; height: 799px; overflow: hidden; }
  body {
    background: var(--backdrop);
    font-family: 'Lato', sans-serif;
    color: var(--ink);
    position: relative;
  }
  .card {
    position: absolute;
    top: 250px;
    width: 520px;
    height: 297px;
    background: var(--card);
    border: 1px solid var(--card-edge);
    box-shadow: 0 14px 30px rgba(0,0,0,.45);
    overflow: hidden;
  }
  .card--back { left: 50px; }
  .card--front { left: 630px; }

  .wordmark {
    position: absolute;
    width: 205px;
    display: flex;
    align-items: center;
    gap: 8px;
    font-weight: 700;
    font-size: 18px;
    letter-spacing: .3px;
    color: var(--ink);
    line-height: 1.1;
    white-space: nowrap;
  }
  .wordmark__square {
    width: 10px; height: 10px;
    background: var(--ink);
    flex: none;
  }
  .card--back .wordmark { left: 30px; top: 136px; color: var(--ink-muted); }
  .card--back .wordmark__square { background: var(--ink-muted); }
  .card--front .wordmark { left: 30px; top: 118px; }

  .mission {
    position: absolute;
    left: 262px;
    top: 40px;
    width: 240px;
    font-weight: 900;
    font-size: 12px;
    line-height: 1.42;
    letter-spacing: .3px;
    white-space: nowrap;
  }
  .mission .lower { font-weight: 700; }
  .rule {
    width: 44px;
    height: 2px;
    background: var(--accent);
    margin: 8px 0 7px;
  }
  .services { list-style: none; font-size: 12px; line-height: 1.45; }
  .services strong { font-weight: 900; }
  .services span { font-weight: 400; color: var(--ink-soft); }
  .since {
    position: absolute;
    right: 22px;
    bottom: 20px;
    font-size: 11px;
    color: var(--ink-soft);
  }

  .person { position: absolute; left: 262px; top: 78px; width: 240px; }
  .person__name { font-weight: 900; font-size: 20px; letter-spacing: .2px; white-space: nowrap; }
  .person__role {
    font-weight: 400; font-size: 11.5px; color: var(--accent);
    letter-spacing: .6px; margin-top: 2px; white-space: nowrap;
  }
  .contacts { list-style: none; margin-top: 14px; font-size: 12.5px; color: var(--ink-soft); }
  .contacts li { display: flex; align-items: center; gap: 9px; line-height: 1.75; }
  .icon { width: 11px; height: 11px; flex: none; }
  .location {
    position: absolute;
    left: 150px;
    bottom: 34px;
    display: flex; align-items: center; gap: 7px;
    font-size: 12.5px; color: var(--ink-soft);
    white-space: nowrap;
  }
</style>
</head>
<body>

  <section class="card card--back" aria-label="Card back">
    <div class="wordmark"><span class="wordmark__square"></span>Velmora Consulting</div>
    <div class="mission">
      <p>EXECUTION</p>
      <p>AS THE OWNER'S REP</p>
      <p>WE AIM TO ACHIEVE YOUR</p>
      <p>INFRASTRUCTURE VISION <span class="lower">with</span></p>
      <p>OUR SPECIALIZATION &amp; EXECUTION <span class="lower">in:</span></p>
      <div class="rule"></div>
      <ul class="services">
        <li><strong>FUNDING</strong> <span>Planning</span></li>
        <li><strong>BUSINESS</strong> <span>Planning</span></li>
        <li><strong>INFRASTRUCTURE</strong> <span>Planning</span></li>
        <li><strong>PROJECT</strong> <span>Management</span></li>
      </ul>
    </div>
    <p class="since">Since 2012</p>
  </section>

  <section class="card card--front" aria-label="Card front">
    <div class="wordmark"><span class="wordmark__square"></span>Velmora Consulting</div>
    <div class="person">
      <h1 class="person__name">Dana Whitcombe-Orr</h1>
      <p class="person__role">CEO / LEAD PROJECT MANAGER</p>
      <ul class="contacts">
        <li>
          <svg class="icon" viewBox="0 0 12 12" aria-hidden="true"><rect x="3" y="0.5" width="6" height="11" rx="1.2" fill="none" stroke="#e0182d" stroke-width="1.3"/><circle cx="6" cy="9.5" r=".7" fill="#e0182d"/></svg>
          867.555.0192
        </li>
        <li>
          <svg class="icon" viewBox="0 0 12 12" aria-hidden="true"><rect x="0.5" y="2.5" width="11" height="7.5" fill="#e0182d"/><path d="M0.5 2.8 6 7 11.5 2.8" fill="none" stroke="#2f2f30" stroke-width="1"/></svg>
          dana@velmora.ca
        </li>
        <li>
          <svg class="icon" viewBox="0 0 12 12" aria-hidden="true"><circle cx="6" cy="6" r="5.5" fill="#e0182d"/><path d="M1 6h10M6 .5c-2.5 3-2.5 8 0 11M6 .5c2.5 3 2.5 8 0 11" fill="none" stroke="#2f2f30" stroke-width=".8"/></svg>
          velmora.ca
        </li>
      </ul>
    </div>
    <p class="location">
      <svg class="icon" viewBox="0 0 12 12" aria-hidden="true"><path d="M6 .5a3.8 3.8 0 0 0-3.8 3.8C2.2 7.2 6 11.5 6 11.5s3.8-4.3 3.8-7.2A3.8 3.8 0 0 0 6 .5z" fill="#e0182d"/><circle cx="6" cy="4.3" r="1.4" fill="#2f2f30"/></svg>
      Northvale NT / Brookmere NB
    </p>
  </section>

</body>
</html>
```